Dwelvano - "Where Pest Control is Free for Life..." Please see pitch deck...

Project goal, that this is a reusable template, not a one-off card
Brand and design direction, follow the logo, use the brand palette (with a color swatch table), typography and layout guidance
The John Doe placeholder content as a clean field-by-field table (name, title, company, address, office, cell, fax, email, dwelvano.com)
Print specs, 3.5 × 2 in trim, 0.125 in bleed, 300 DPI, CMYK, crop marks
Deliverables, layered editable PSD (your primary ask) plus vector .AI/.EPS and a press-ready PDF/X-1a, with fonts packaged
What you'll provide (logo, colors, fonts)
Process and sign-off, concept first, then full file package on approval.
Populate every field with this John Doe placeholder data so we can see the layout fully built out. We will replace it per person.
Name John Doe
Title Title / Position
Company Dwelvano
Address 123 Main Street, Suite 100, Tallahassee, FL 32301
Office (850) 555-0100
Cell (850) 555-0123
Fax (850) 555-0199
Email johndoe@dwelvano.com
Website dwelvano.com

We need the working, editable source files so we can update them ourselves, plus a ready-to-print export:
1. Photoshop (.PSD) — fully layered and editable, with each contact field on its own labeled text layer. This is the primary requested format.
2. Vector source — the press-standard editable format, Adobe Illustrator (.AI) and/or .EPS, since vector is preferred for crisp text and logos at print.
3. Print-ready PDF — press-quality (PDF/X-1a), CMYK, with bleed and crop marks, both sides.
4. Packaged fonts and links — include or list all fonts used, and package any linked assets so the files open correctly on our end.

Why both PSD and vector
The PSD covers our request directly and is easy for us to edit. Vector (.AI/.EPS) is what most commercial printers actually prefer for type and logos because it stays razor-sharp at any size. Providing both keeps us flexible no matter which printer we use. Have fun and keep it modern and cool the designer of the logo did a great job, see what you can do.

```html
<!DOCTYPE html>
<html lang="en">
<head>
<meta charset="utf-8">
<title>Dwelvano Business Card</title>
<link rel="stylesheet" href="https://fonts.googleapis.com/css2?family=Poppins:wght@300;400;500;600;700;800&display=swap">
<style>
  :root {
    --bg: #5e5e5e;
    --card: #1e1e1f;
    --card-deep: #0c0c0d;
    --teal: #08b3c6;
    --white: #ffffff;
    --shadow: rgba(0, 0, 0, 0.45);
  }
  * { margin: 0; padding: 0; box-sizing: border-box; }
  html, body {
    width: 1200px; height: 800px; overflow: hidden;
    background: var(--bg);
    font-family: "Poppins", sans-serif;
  }
  .canvas {
    position: relative; width: 1200px; height: 800px;
    display: flex; align-items: center; justify-content: center; gap: 40px;
  }
  .card {
    position: relative; width: 540px; height: 309px;
    background: var(--card);
    border-radius: 26px;
    border: 4px solid var(--teal);
    box-shadow: 0 14px 30px var(--shadow);
    overflow: hidden;
  }

  /* Front */
  .card--front { display: flex; align-items: center; justify-content: center; }
  .brand {
    display: flex; align-items: center; gap: 10px;
    font-weight: 800; color: var(--white); letter-spacing: -1px; line-height: 1;
  }
  .brand__mark { background: var(--teal); display: inline-block; }
  .card--front .brand { font-size: 72px; }
  .card--front .brand__mark { width: 22px; height: 22px; }

  /* Back */
  .feature-panel {
    position: absolute; top: 0; right: 0; bottom: 0; width: 52%;
    background: linear-gradient(160deg, #2a2a2b 0%, var(--card-deep) 55%, #050505 100%);
    clip-path: polygon(22% 0, 100% 0, 100% 100%, 12% 100%, 0 55%);
  }
  .edge-band {
    position: absolute; top: 0; right: 0; bottom: 0; width: 16px;
    background: var(--teal);
  }
  .info { position: absolute; left: 26px; top: 20px; width: 300px; }
  .card--back .brand { font-size: 46px; }
  .card--back .brand__mark { width: 14px; height: 14px; }
  .tagline {
    margin-top: 4px;
    font-size: 11px; font-weight: 700; letter-spacing: 1.2px; color: var(--white);
  }
  .subline { font-size: 10.5px; font-weight: 300; color: var(--teal); letter-spacing: 0.3px; }

  .identity { position: relative; margin-top: 12px; }
  .identity__accent {
    position: absolute; left: -30px; top: 2px; width: 12px; height: 44px;
    background: var(--teal);
  }
  .name { font-size: 24px; line-height: 1.05; }
  .name__first { color: var(--teal); font-weight: 600; }
  .name__last { color: var(--white); font-weight: 300; }
  .position { font-size: 12px; font-weight: 500; color: var(--white); margin-top: 2px; }

  .address { margin-top: 7px; font-size: 11.5px; font-weight: 400; color: var(--white); line-height: 1.35; }

  .contacts { list-style: none; margin-top: 7px; }
  .contacts li {
    display: flex; align-items: center; gap: 8px;
    font-size: 11.5px; color: var(--white); line-height: 16.5px;
  }
  .contacts svg { width: 12px; height: 12px; flex: none; }
</style>
</head>
<body>
<main class="canvas">

  <section class="card card--front" aria-label="Card front">
    <div class="brand"><span class="brand__mark"></span>Dwelvano</div>
  </section>

  <section class="card card--back" aria-label="Card back">
    <div class="feature-panel"></div>
    <div class="edge-band"></div>

    <div class="info">
      <div class="brand"><span class="brand__mark"></span>Dwelvano</div>
      <p class="tagline">WE SERVE WHERE YOU LIVE</p>
      <p class="subline">Friendly local home care</p>

      <div class="identity">
        <span class="identity__accent"></span>
        <p class="name"><span class="name__first">John</span> <span class="name__last">Doe</span></p>
        <p class="position">Title / Position</p>
      </div>

      <p class="address">123 Main Street, Suite 100,<br>Tallahassee, FL 32301</p>

      <ul class="contacts">
        <li>
          <svg viewBox="0 0 24 24" fill="var(--teal)"><path d="M6.6 10.8a15.1 15.1 0 0 0 6.6 6.6l2.2-2.2a1 1 0 0 1 1-.25 11.4 11.4 0 0 0 3.6.57 1 1 0 0 1 1 1V20a1 1 0 0 1-1 1A17 17 0 0 1 3 4a1 1 0 0 1 1-1h3.5a1 1 0 0 1 1 1c0 1.25.2 2.45.57 3.57a1 1 0 0 1-.25 1z"/></svg>
          (850) 555-0100
        </li>
        <li>
          <svg viewBox="0 0 24 24" fill="none" stroke="var(--teal)" stroke-width="2"><rect x="6" y="2" width="12" height="20" rx="2"/><line x1="11" y1="18" x2="13" y2="18"/></svg>
          (850) 555-0123
        </li>
        <li>
          <svg viewBox="0 0 24 24" fill="var(--teal)"><rect x="7" y="2" width="10" height="7"/><rect x="3" y="9" width="18" height="9" rx="1"/><rect x="7" y="15" width="10" height="7"/></svg>
          (850) 555-0199
        </li>
        <li>
          <svg viewBox="0 0 24 24" fill="none" stroke="var(--teal)" stroke-width="2"><circle cx="12" cy="12" r="9"/><ellipse cx="12" cy="12" rx="4" ry="9"/><line x1="3" y1="12" x2="21" y2="12"/></svg>
          dwelvano.com
        </li>
        <li>
          <svg viewBox="0 0 24 24" fill="none" stroke="var(--teal)" stroke-width="2"><rect x="3" y="5" width="18" height="14" rx="1"/><polyline points="3,6 12,13 21,6"/></svg>
          johndoe@dwelvano.com
        </li>
      </ul>
    </div>
  </section>

</main>
</body>
</html>
```